Web Developer Needs a Business Card Design

I need a personal business card design that represents me as a web developer for potential employers. I would like the background to be a dark color on the front for contrast with my logo and name. The back will have all my information along with a smaller version of the logo. I want something with a modern look and feel, not too conservative. This will be used for potential employers and freelance work.

Industry/Entity Type

Business

Contact Information for Business Card

Front should have my logo and name. The back should have all my personal information which would include: name: Tom Varulek, phone: 570-614-3098, email: tomvarulek@quillbox.net, website url: www.tomvarulek.net, logo, web developer.

Font styles to use
Sans Serif

Requirements
Must have
• Must include my logo. The color palette base color will be the logo color.

```html
<!DOCTYPE html>
<html lang="en">
<head>
<meta charset="utf-8">
<title>Tom Varulek – Business Card</title>
<link rel="stylesheet" href="https://fonts.googleapis.com/css2?family=Questrial&display=swap">
<style>
  :root {
    --page-bg: #d9d6d1;
    --card-bg-top: #f1f3f2;
    --card-bg-bottom: #e2e6e4;
    --brand-green: #22b584;
    --brand-green-light: #3fd0a2;
    --brand-green-dark: #1c9e74;
    --ink: #2e3432;
    --ink-soft: #3a403e;
  }
  * { margin: 0; padding: 0; box-sizing: border-box; }
  html, body {
    width: 1200px;
    height: 969px;
    overflow: hidden;
    background: var(--page-bg);
    font-family: "Questrial", "Century Gothic", sans-serif;
  }
  .card {
    position: absolute;
    left: 100px;
    top: 200px;
    width: 1000px;
    height: 568px;
    overflow: hidden;
    background: linear-gradient(170deg, var(--card-bg-top), var(--card-bg-bottom));
    box-shadow: 0 18px 40px rgba(0,0,0,0.18);
  }
  .card__shapes {
    position: absolute;
    inset: 0;
  }
  .identity {
    position: absolute;
    left: 58px;
    top: 306px;
    color: var(--ink);
  }
  .identity__name {
    font-size: 46px;
    font-weight: 400;
    line-height: 1;
    letter-spacing: 0.5px;
  }
  .identity__role {
    margin-top: 14px;
    font-size: 27px;
    line-height: 1;
    color: var(--ink-soft);
  }
  .contact {
    position: absolute;
    left: 58px;
    top: 424px;
    list-style: none;
    color: var(--ink-soft);
    font-size: 25px;
  }
  .contact__item {
    display: flex;
    align-items: center;
    height: 38px;
  }
  .contact__icon {
    width: 22px;
    height: 22px;
    margin-right: 16px;
    flex: none;
  }
  .monogram {
    position: absolute;
    left: 706px;
    top: 40px;
    width: 236px;
    height: 236px;
    border: 7px solid var(--brand-green);
    border-radius: 50%;
    display: flex;
    align-items: center;
    justify-content: center;
    color: var(--brand-green);
    font-size: 40px;
    letter-spacing: 1px;
  }
  .social {
    position: absolute;
    right: 60px;
    top: 476px;
    display: flex;
    gap: 22px;
    list-style: none;
    color: var(--brand-green-dark);
    font-size: 21px;
  }
</style>
</head>
<body>
  <main class="card">
    <svg class="card__shapes" width="1000" height="568" viewBox="0 0 1000 568" aria-hidden="true">
      <defs>
        <linearGradient id="badgeFill" x1="0" y1="0" x2="0" y2="1">
          <stop offset="0" stop-color="var(--brand-green-light)"/>
          <stop offset="1" stop-color="var(--brand-green-dark)"/>
        </linearGradient>
      </defs>
      <circle cx="136" cy="560" r="384" fill="none" stroke="var(--brand-green)" stroke-width="6"/>
      <circle cx="136" cy="560" r="364" fill="url(#badgeFill)"/>
    </svg>

    <section class="identity">
      <h1 class="identity__name">Tom Varulek</h1>
      <p class="identity__role">Front-End Developer</p>
    </section>

    <ul class="contact">
      <li class="contact__item">
        <svg class="contact__icon" viewBox="0 0 24 24" aria-hidden="true"><path fill="currentColor" d="M6.6 10.8a15.1 15.1 0 0 0 6.6 6.6l2.2-2.2c.3-.3.7-.4 1-.2 1.1.4 2.3.6 3.6.6.6 0 1 .4 1 1V20c0 .6-.4 1-1 1A17 17 0 0 1 3 4c0-.6.4-1 1-1h3.5c.6 0 1 .4 1 1 0 1.3.2 2.5.6 3.6.1.3 0 .7-.2 1z"/></svg>
        570-614-3098
      </li>
      <li class="contact__item">
        <svg class="contact__icon" viewBox="0 0 24 24" aria-hidden="true"><path fill="currentColor" d="M2 5h20v14H2zM3.5 6.5v.4l8.5 6 8.5-6v-.4z"/></svg>
        tomvarulek@quillbox.net
      </li>
      <li class="contact__item">
        <svg class="contact__icon" viewBox="0 0 24 24" aria-hidden="true"><circle cx="12" cy="12" r="10" fill="currentColor"/><path d="M2 12h20M12 2c3 3 3 17 0 20M12 2c-3 3-3 17 0 20" stroke="#e4e8e6" stroke-width="1.4" fill="none"/></svg>
        www.tomvarulek.net
      </li>
    </ul>

    <div class="monogram">Varulek</div>

    <ul class="social">
      <li>Chirrup</li>
      <li>Linkwork</li>
      <li>Codehub</li>
    </ul>
  </main>
</body>
</html>
```